Brochure for a website accessibility report

This brochure is related to a report that www.qelvantrix.org sell. The report shows the results of an automated audit of a websites accessibility. It shows details of issues found with screen shots, examples of code and provides remediation advice.

The brochure will be a pdf 8.5 inches by 11 inches. It can be anywhere from 6 to 10 pages.

The FlintVue™ name itself should be “Bree Serif” font. The fonts, styles, colors and sizes are up to you.

The images used and logo of the Office of Digital Reachworks and K7P logo are upload

We highlighted in blue page extracts from the report we sell. Do not use the blue highlight, it is merely there to show you where the specific examples of the report we sell are vs the other content in the report. The areas in blue which show the content from the actual report should be shown as an extract of the actual page of the report. You have flexibility to change the layout and the way the content look.

The red square callouts over the blue content are callouts that describe the specific page extracts. We used it as a red callout only so that you would be able to see it. You should change the specific location, look and feel of the callout to be appropriate

Target Market(s)

Marketing and Technical people

Industry/Entity Type

Information Technology

Font styles to use
Sans Serif

Colors

Designer to choose colors to be used in the design.

Requirements
Should not have
• wheelchairs, images of blind people

```html
<!DOCTYPE html>
<html lang="en">
<head>
<meta charset="utf-8">
<title>Structure – Report Page Extract</title>
<link rel="stylesheet" href="https://fonts.googleapis.com/css2?family=Bree+Serif&family=Roboto:wght@300;400;500&family=Roboto+Slab:wght@300;400&display=swap">
<style>
  :root {
    --navy: #0d3a5c;
    --panel: #3589c3;
    --yellow: #f6cb3c;
    --gold-text: #f2c838;
    --cyan: #45d3ea;
    --ink: #0d3a5c;
    --white: #ffffff;
    --code-bg: #e9ebed;
    --code-ink: #2a3440;
  }
  * { margin: 0; padding: 0; box-sizing: border-box; }
  html, body { width: 927px; height: 1200px; overflow: hidden; background: var(--white); }
  body { position: relative; font-family: "Roboto", sans-serif; color: var(--white); }

  .page-card {
    position: absolute; left: 53px; top: 51px; width: 820px; height: 1093px;
    background: var(--navy); border-radius: 62px;
  }
  .shapes { position: absolute; left: 0; top: 0; width: 927px; height: 1200px; }
  .abs { position: absolute; }

  .section-title {
    left: 103px; top: 72px; font-family: "Bree Serif", serif; font-size: 33px; font-weight: 400;
    color: var(--yellow);
  }
  .intro { left: 103px; top: 133px; font-size: 16.4px; font-weight: 300; }
  .rules { left: 103px; top: 162px; width: 664px; list-style: none; font-size: 16.4px; font-weight: 300; line-height: 20px; }
  .rules li { position: relative; padding-left: 32px; margin-bottom: 10px; }
  .rules li::before {
    content: ""; position: absolute; left: 0; top: 7px; width: 6px; height: 6px; background: var(--cyan);
  }

  .issue-heading { left: 103px; top: 358px; font-size: 16.4px; font-weight: 500; }
  .issue-heading span { color: var(--gold-text); }
  .issue-body {
    left: 103px; top: 381px; width: 718px; font-size: 16.6px; font-weight: 300; line-height: 25.6px;
    text-align: justify;
  }
  .checkpoints { left: 103px; top: 486px; font-size: 16.4px; font-weight: 300; }
  .checkpoints .ref { color: var(--gold-text); margin-left: 18px; }

  .sub-heading { font-size: 16.4px; font-weight: 500; }
  .remedy-heading { left: 103px; top: 531px; }
  .remedy-body {
    left: 103px; top: 555px; width: 718px; font-size: 16.4px; font-weight: 300; line-height: 25.6px;
    text-align: justify;
  }
  .remedy-body code { font-family: "Roboto Slab", serif; color: var(--gold-text); font-size: 16px; font-weight: 300; }
  .reading-heading { left: 103px; top: 654px; }
  .reading-links { left: 153px; top: 674px; font-size: 16.4px; font-weight: 300; line-height: 20px; color: var(--cyan); list-style: none; }

  .callout {
    position: absolute; color: var(--ink); font-size: 14.2px; font-weight: 400; letter-spacing: 0.8px;
    text-transform: uppercase; line-height: 19px;
  }
  .callout-checkpoint { left: 551px; top: 489px; width: 292px; }
  .callout-screens { left: 399px; top: 668px; width: 444px; }

  .example-panel {
    position: absolute; left: 83px; top: 743px; width: 758px; height: 367px;
    background: var(--panel); border-radius: 27px;
  }
  .example-heading { left: 103px; top: 759px; font-size: 16.4px; font-weight: 500; }
  .example-heading span { font-weight: 300; margin-left: 8px; }
  .specific-heading { left: 104px; top: 801px; font-size: 16.4px; font-weight: 500; }
  .specific-body {
    left: 104px; top: 822px; width: 508px; font-size: 16.4px; font-weight: 300; line-height: 23px;
    text-align: justify;
  }
  .specific-body em { font-style: normal; font-family: "Roboto Slab", serif; font-weight: 300; color: var(--gold-text); font-size: 15.5px; }
  .site-preview {
    left: 632px; top: 803px; width: 189px; height: 197px;
    background: linear-gradient(180deg, #1d3552 0 9%, #c9b48a 9% 15%, #f4f4f2 15% 88%, #1b2f4a 88% 100%);
    border: 1px solid #d8d8d8;
  }
  .snippet-heading { left: 104px; top: 916px; font-size: 16.4px; font-weight: 500; }
  .code-snippet {
    left: 103px; top: 947px; width: 509px; height: 142px; background: var(--code-bg);
    border: 1px solid #c9cdd2; padding: 7px 11px; font-family: "Roboto Slab", serif; font-weight: 300;
    font-size: 11.4px; line-height: 16.3px; color: var(--code-ink); text-transform: uppercase;
    text-align: justify; overflow-wrap: break-word;
  }
</style>
</head>
<body>
  <div class="page-card"></div>
  <div class="example-panel"></div>

  <svg class="shapes" viewBox="0 0 927 1200" aria-hidden="true">
    <path d="M541 459 H836 Q856 459 856 479 V532 Q856 552 836 552 H541 Q519 552 519 530 V525 L426 497 L519 481 V481 Q519 459 541 459 Z" fill="var(--yellow)"/>
    <path d="M390 640 H836 Q856 640 856 660 V712 Q856 732 836 732 H826 L808 812 L790 732 H390 Q368 732 368 710 V662 Q368 640 390 640 Z" fill="var(--yellow)"/>
  </svg>

  <h1 class="abs section-title">Structure</h1>
  <p class="abs intro">Ensure that your HTML layout structuring is necessary and informative.</p>
  <ul class="abs rules">
    <li>Use tables appropriately; layout tables should not use table grouping/organization tags but data/list-like content tables should use grouping tags.</li>
    <li>Frames should be properly organized, titled and identified. Aria Roles should be used where relevant.</li>
    <li>Layout or structural imagery must not have a title-attribute and should have an empty alt-attribute.</li>
    <li>Instructive content should be provided along with skip-links as necessary.</li>
  </ul>

  <h2 class="abs issue-heading">ISSUE: <span>LAYOUT TABLE WITH SUMMARY (PRIORITY 4)</span></h2>
  <p class="abs issue-body">The summary attribute on a layout table should be empty. The purpose of a layout table is simply to control the placement of content; the table itself is transparent to the user. A summary attribute would break this transparency by calling attention to the table. A null summary (summary="") on layout tables is acceptable.</p>
  <p class="abs checkpoints">Issue is relevant to checkpoints: <span class="ref">1.3.1 (A).</span></p>

  <p class="callout callout-checkpoint">Each issue is detailed with links to the specific DARG checkpoint</p>

  <h3 class="abs sub-heading remedy-heading">General Remediation Advice:</h3>
  <p class="abs remedy-body">Remove the <code>summary</code> attribute from tables used solely for layout. It should only be used for tables that present tabular data. In HTML 5, you can use the <code>role</code> attribute on the <code>TABLE</code> with a value of "presentation" to explicitly mark the table as being used for layout.</p>

  <h3 class="abs sub-heading reading-heading">Suggested Reading:</h3>
  <ul class="abs reading-links">
    <li>Adaptable</li>
    <li>Info and Relationships</li>
  </ul>

  <p class="callout callout-screens">Appropriate screenshots with the issue highlighted are shown where the issue resides on the webpage</p>

  <h3 class="abs example-heading">EXAMPLE 1 OF 6: <span>HTTP://WWW.VARNOSTA.ORG/ES/DOCUMENTS/SC/XCHGESC.SHTML</span></h3>
  <h4 class="abs specific-heading">SPECIFIC ISSUES:</h4>
  <p class="abs specific-body">Layout tables should not have a 'SUMMARY' attribute; or it should be an empty text value. <em>&lt;TABLE&gt; Tag</em> found <em>summary='La tabla debe ser leída por fila. Tiene tres filas, cada una representa u...</em></p>
  <div class="abs site-preview" role="img" aria-label="Screenshot of the audited webpage with the layout table highlighted"></div>

  <h4 class="abs snippet-heading">CODE SNIPPET</h4>
  <p class="abs code-snippet">&lt;TABLE CLASS="YRLIST" SUMMARY="LA TABLA DEBE SER LE&amp;#237;DA POR FILA. TIENE TRES FILAS, CADA UNA REPRESENTA UNA D&amp;#233;CADA, LA FILA DE ARRIBA ES DE LA D&amp;#233;CADA ACTUAL. LOS V&amp;#237;NCULOS DE LOS A&amp;#241;OS EN CADA CELDA DE LA TABLA ABRIR&amp;#225;N UNA P&amp;#225;GINA CON LA LISTA DE CARTAS INTERCAMBIADAS DURANTE ESE A&amp;#241;O EN PARTICULAR."&gt; &lt;TBODY&gt;&lt;TR&gt; &lt;TH COLSPAN="11" CLASS="TBLTITLE"&gt;INTER-CAMBIO DE CARTAS DEL DIRECTOR EJECUTIVO Y EL PRESIDENTE DEL CONSEJO DE VARNOSTA&lt;/TH&gt;</p>
</body>
</html>
```